professional business card design for technology company

We are a small technology consulting firm, specialising in consulting based around Cloud and Managed services. Our colour scheme is yellow, blue and white, as you can see in the logos. Although we are based in melbourne australia, due to the nature of our work, our clients can be located anywhere. We are looking for a clean, professional, positive look - similar to our company logo

Target Market(s)

small business

Industry/Entity Type

Business

Contact Information for Business Card

eye catching, designed to incorporate some level of raised printing. Must contain website address, phone number, name and job title

Requirements
Must have
• Logo (attached) - use of the same colour scheme

```html
<!DOCTYPE html>
<html lang="en">
<head>
<meta charset="utf-8">
<title>Nimbara Business Card</title>
<link href="https://fonts.googleapis.com/css2?family=Montserrat:wght@400;600;700&family=Open+Sans:wght@400;600&display=swap" rel="stylesheet">
<style>
  :root {
    --blue: #1f9bd1;
    --blue-deep: #1b93c9;
    --paper: #f1f1f1;
    --ink: #4a4a4a;
    --ink-soft: #5e5656;
    --sun: #f2cd00;
    --backdrop: #e4e6e8;
  }
  * { margin: 0; padding: 0; box-sizing: border-box; }
  html, body { width: 1200px; height: 960px; overflow: hidden; }
  body {
    background: var(--backdrop);
    font-family: "Open Sans", Arial, sans-serif;
    position: relative;
  }
  .card {
    position: absolute;
    left: 250px;
    width: 700px;
    height: 400px;
    background: var(--paper);
    overflow: hidden;
    box-shadow: 0 6px 18px rgba(0,0,0,0.12);
  }
  .card--front { top: 40px; }
  .card--back { top: 520px; }

  /* Front */
  .front__top-strip {
    position: absolute; left: 0; top: 0; width: 100%; height: 10px;
    background: var(--blue);
  }
  .front__band {
    position: absolute; left: 0; bottom: 0; width: 100%; height: 104px;
    background: var(--blue);
    display: flex; align-items: center; justify-content: center; gap: 10px;
  }
  .front__web {
    color: #fff; font-size: 15px; letter-spacing: 1.5px;
  }
  .brand {
    display: flex; align-items: center; gap: 22px;
  }
  .brand__dot {
    border-radius: 50%; background: var(--blue);
  }
  .brand__name {
    font-family: "Montserrat", Arial, sans-serif;
    font-weight: 700;
    color: var(--ink);
    letter-spacing: -1px;
  }
  .front__brand {
    position: absolute; left: 0; right: 0; top: 118px;
    justify-content: center;
  }
  .front__brand .brand__dot { width: 64px; height: 64px; }
  .front__brand .brand__name { font-size: 80px; line-height: 1; }

  /* Back */
  .back__brand {
    position: absolute; left: 40px; top: 62px;
    gap: 14px;
  }
  .back__brand .brand__dot { width: 34px; height: 34px; }
  .back__brand .brand__name { font-size: 46px; line-height: 1; }

  .back__panel-top {
    position: absolute; left: 356px; top: 0; width: 344px; height: 66px;
    background: var(--blue-deep);
  }
  .back__panel-main {
    position: absolute; left: 328px; top: 148px; width: 372px; height: 252px;
    background: var(--blue-deep);
  }
  .back__identity {
    position: absolute; left: 390px; top: 90px;
  }
  .back__name {
    font-family: "Montserrat", Arial, sans-serif;
    font-size: 21px; letter-spacing: 0.5px;
    color: var(--ink); font-weight: 700;
  }
  .back__name span { color: var(--blue); font-weight: 400; }
  .back__title {
    font-family: "Montserrat", Arial, sans-serif;
    font-size: 14px; color: var(--blue); letter-spacing: 0.5px;
  }
  .contact {
    position: absolute; left: 372px; top: 196px;
    list-style: none;
    display: flex; flex-direction: column; gap: 16px;
  }
  .contact__item {
    display: flex; align-items: center; gap: 18px;
    color: var(--ink-soft); font-size: 15px; font-weight: 600;
  }
  .contact__icon {
    width: 32px; height: 32px; border-radius: 5px;
    background: #fff; display: flex; align-items: center; justify-content: center;
  }
</style>
</head>
<body>

<section class="card card--front" aria-label="Business card front">
  <div class="front__top-strip"></div>
  <div class="brand front__brand">
    <div class="brand__dot"></div>
    <div class="brand__name">Nimbara</div>
  </div>
  <div class="front__band">
    <svg width="14" height="14" viewBox="0 0 14 14" aria-hidden="true">
      <circle cx="7" cy="7" r="6.5" fill="#fff"/>
      <path d="M3 5 Q5 3 7 5 T10 8 Q8 11 6 9 Z" fill="#1f9bd1"/>
    </svg>
    <span class="front__web">www.nimbara.com</span>
  </div>
</section>

<section class="card card--back" aria-label="Business card back">
  <div class="brand back__brand">
    <div class="brand__dot"></div>
    <div class="brand__name">Nimbara</div>
  </div>
  <div class="back__panel-top"></div>
  <div class="back__panel-main"></div>
  <div class="back__identity">
    <div class="back__name">DORIAN K. <span>VALE</span></div>
    <div class="back__title">PRINCIPAL</div>
  </div>
  <ul class="contact">
    <li class="contact__item">
      <span class="contact__icon">
        <svg width="18" height="18" viewBox="0 0 24 24" aria-hidden="true"><path d="M6.6 10.8a15 15 0 0 0 6.6 6.6l2.2-2.2c.3-.3.7-.4 1-.2 1.1.4 2.3.6 3.6.6.6 0 1 .4 1 1V20c0 .6-.4 1-1 1C10.6 21 3 13.4 3 4c0-.6.4-1 1-1h3.5c.6 0 1 .4 1 1 0 1.3.2 2.5.6 3.6.1.3 0 .7-.2 1z" fill="#1f9bd1"/></svg>
      </span>
      305-555-0182
    </li>
    <li class="contact__item">
      <span class="contact__icon">
        <svg width="18" height="18" viewBox="0 0 24 24" aria-hidden="true"><rect x="2" y="5" width="20" height="14" rx="1.5" fill="#1f9bd1"/><path d="M3 6l9 7 9-7" stroke="#fff" stroke-width="1.6" fill="none"/></svg>
      </span>
      DorianKVale@nimbara.com
    </li>
    <li class="contact__item">
      <span class="contact__icon">
        <svg width="18" height="18" viewBox="0 0 24 24" aria-hidden="true"><circle cx="12" cy="12" r="10" fill="#1f9bd1"/><path d="M6 9 Q9 5 12 8 T17 12 Q14 18 10 14 Z" fill="#fff"/></svg>
      </span>
      www.nimbara.com
    </li>
  </ul>
</section>

</body>
</html>
```